Veldmark Supplies Business Card

Professional business card that stand out to our potential customers. Front and back with clean modern design

Industry/Entity Type

Oil and gas

Contact Information for Business Card

Name, address, website , office phone and cell number

Requirements
Must have
• Editable files for each employee

```html
<!DOCTYPE html>
<html lang="en">
<head>
<meta charset="UTF-8">
<title>Veldmark Supplies Business Card</title>
<link rel="stylesheet" href="https://fonts.googleapis.com/css2?family=Montserrat:wght@400;500;700&display=swap">
<style>
  :root {
    --stage: #3b3b3c;
    --ink: #231f20;
    --paper: #ffffff;
    --red: #ed1c24;
    --cyan: #0fb0d3;
    --text-light: #ffffff;
  }
  * { box-sizing: border-box; margin: 0; padding: 0; }
  html, body { width: 1200px; height: 1059px; overflow: hidden; }
  body {
    background: var(--stage);
    font-family: "Montserrat", Arial, sans-serif;
    position: relative;
  }
  .card {
    position: absolute;
    left: 256px;
    width: 690px;
    height: 392px;
    overflow: hidden;
  }
  .card--front { top: 100px; background: var(--paper); }
  .card--back { top: 537px; background: var(--ink); }
  .wave { position: absolute; inset: 0; width: 100%; height: 100%; }

  .brand {
    position: absolute;
    display: flex;
    align-items: center;
    gap: 8px;
    font-weight: 700;
    color: var(--red);
    white-space: nowrap;
  }
  .brand__mark { background: var(--cyan); flex: none; }
  .card--front .brand { right: 32px; top: 78px; font-size: 22px; }
  .card--front .brand__mark { width: 18px; height: 18px; }
  .card--back .brand {
    left: 50%; top: 50%; transform: translate(-50%, -50%);
    font-size: 38px; gap: 14px;
  }
  .card--back .brand__mark { width: 30px; height: 30px; }

  .person { position: absolute; left: 35px; top: 192px; }
  .person__name { font-size: 28px; font-weight: 700; line-height: 1; letter-spacing: 0.2px; }
  .person__first { color: var(--red); }
  .person__last { color: var(--cyan); }
  .person__role { color: var(--text-light); font-size: 15px; font-weight: 400; margin-top: 6px; letter-spacing: 0.3px; }
  .person__rule { width: 13px; height: 2px; background: var(--red); margin-top: 15px; }

  .contacts { position: absolute; left: 35px; top: 267px; list-style: none; }
  .contacts li {
    display: flex; align-items: center; gap: 8px;
    height: 23.3px;
    color: var(--text-light); font-size: 16px; letter-spacing: 0.3px;
  }
  .contacts svg { width: 13px; height: 13px; flex: none; }

  .location {
    position: absolute; right: 28px; top: 338px;
    display: flex; align-items: center; gap: 10px;
    color: var(--text-light); font-size: 16px; letter-spacing: 0.3px;
  }
  .location svg { width: 11px; height: 16px; }
</style>
</head>
<body>
  <section class="card card--front">
    <svg class="wave" viewBox="0 0 690 392" preserveAspectRatio="none" aria-hidden="true">
      <path fill="var(--ink)" d="M0 209 C60 142 170 128 260 150 C380 180 460 276 567 280 C630 283 672 252 690 212 L690 392 L0 392 Z"/>
      <path fill="var(--red)" d="M114 137 C250 122 380 205 480 238 C560 264 655 262 690 171 L690 203 C660 262 580 272 500 255 C400 232 260 126 114 137 Z"/>
    </svg>

    <div class="brand"><span class="brand__mark"></span>Veldmark Supplies</div>

    <div class="person">
      <h1 class="person__name"><span class="person__first">Daniel</span> <span class="person__last">Morrow</span></h1>
      <p class="person__role">Manager</p>
      <div class="person__rule"></div>
    </div>

    <ul class="contacts">
      <li>
        <svg viewBox="0 0 16 16" aria-hidden="true"><path fill="var(--red)" d="M3.5 1.5l2.3 2.8-1.4 1.7c.9 2 2.5 3.6 4.5 4.5l1.7-1.4 2.8 2.3-1.5 2.1C6.9 13.6 2.4 9.1 1.5 3z"/></svg>
        1-604-555-0148
      </li>
      <li>
        <svg viewBox="0 0 16 16" aria-hidden="true"><rect x="1" y="3" width="14" height="10" rx="1" fill="var(--cyan)"/><path d="M1.5 4l6.5 5 6.5-5" stroke="var(--ink)" stroke-width="1.2" fill="none"/></svg>
        dmorrow@veldmarksupply.vn
      </li>
      <li>
        <svg viewBox="0 0 16 16" aria-hidden="true"><g fill="none" stroke="var(--red)" stroke-width="1.3"><circle cx="8" cy="8" r="6.5"/><ellipse cx="8" cy="8" rx="3" ry="6.5"/><path d="M1.5 8h13M2.5 4.8h11M2.5 11.2h11"/></g></svg>
        www.veldmarksupply.vn
      </li>
      <li>
        <svg viewBox="0 0 16 16" aria-hidden="true"><g fill="none" stroke="var(--cyan)" stroke-width="1.3"><circle cx="8" cy="8" r="6.5"/><ellipse cx="8" cy="8" rx="3" ry="6.5"/><path d="M1.5 8h13M2.5 4.8h11M2.5 11.2h11"/></g></svg>
        www.veldmarksupply.com
      </li>
    </ul>

    <div class="location">
      Ho Chi Minh, Vietnam
      <svg viewBox="0 0 11 16" aria-hidden="true"><path fill="var(--red)" d="M5.5 0C2.5 0 0 2.4 0 5.4 0 9.3 5.5 16 5.5 16S11 9.3 11 5.4C11 2.4 8.5 0 5.5 0z"/><circle cx="5.5" cy="5.4" r="2" fill="var(--ink)"/></svg>
    </div>
  </section>

  <section class="card card--back">
    <div class="brand"><span class="brand__mark"></span>Veldmark Supplies</div>
  </section>
</body>
</html>
```